3D Printing Website redesign

We are in the process of redesigning our website. Attached is an image of one of the proposed pages - "The Quillmarrow". The idea with this page is that site visitors can get an indicative estimate of the cost of 3D Printing based on some provided metrics. When the user alters the metrics the price changes accordingly. We are looking for a design to support this page that will also be used across our site.

Reason: Allow more time for designers to submit designs

Reason: Still looking for the design to blow us away!

Printing

```html
<!DOCTYPE html>
<html lang="en">
<head>
<meta charset="utf-8">
<title>Layerforge Studio — Pricing &amp; Quote</title>
<link rel="stylesheet" href="https://fonts.googleapis.com/css2?family=Rambla:wght@400;700&family=Open+Sans:wght@400;600;700&family=Arimo:wght@400;700&display=swap">
<style>
:root{
  --blue-top:#1b88cf;
  --blue-bottom:#0a58a6;
  --accent:#1a8ad6;
  --navy:#0d3a6e;
  --ink:#555a60;
  --muted:#7b8087;
  --panel:#efefef;
  --line:#cfd2d6;
  --white:#ffffff;
  --foot:#3e4044;
  --foot-dark:#242526;
  --foot-text:#e3e5e8;
  --orange:#f08a4b;
}
*{box-sizing:border-box;margin:0;padding:0}
html,body{width:1024px;height:1200px;overflow:hidden}
body{position:relative;background:var(--panel);font-family:"Rambla",sans-serif;color:var(--ink)}
.abs{position:absolute}

/* header */
.topbar{left:0;top:0;width:1024px;height:8px;background:#d3d7da}
.account-tab{left:744px;top:0;width:136px;height:20px;background:#d3d7da;border-radius:0 0 6px 6px;font:600 9px/20px "Open Sans",sans-serif;color:var(--navy);display:flex;justify-content:center;gap:14px}
.header{left:0;top:8px;width:1024px;height:96px;background:var(--white)}
.brand{left:140px;top:20px;display:flex;align-items:center;gap:10px}
.brand-mark{width:70px;height:70px;border-radius:50%;background:#6f8aa5}
.brand-name{font:700 22px/1 "Rambla",sans-serif;color:#1f6fb8;letter-spacing:.3px}
.social-top{top:32px;width:18px;height:18px;border-radius:50%;background:#2c66a8}
.call{left:686px;top:32px;font-size:13px;color:#8a8f95;display:flex;align-items:center;gap:6px}
.call b{color:var(--navy)}
.nav{left:430px;top:64px;width:456px;display:flex;justify-content:space-between;font-size:11.4px;color:#6b7077}
.nav .sep{color:#a8adb3}
.nav .active{color:var(--accent)}
.nav-pointer{left:584px;top:93px;width:0;height:0;border-left:11px solid transparent;border-right:11px solid transparent;border-bottom:11px solid var(--blue-top)}

/* quote band */
.quote{left:0;top:104px;width:1024px;height:392px;background:linear-gradient(180deg,var(--blue-top),var(--blue-bottom))}
.quote-title{left:0;top:18px;width:1044px;text-align:center;font-size:24px;color:var(--white);letter-spacing:.4px}
.mode-btn{left:136px;width:192px;height:60px;background:linear-gradient(#fff,#ececec);border-radius:3px;box-shadow:0 2px 0 #a9c6e3;display:flex;align-items:center;justify-content:center;gap:12px;font-size:24px;color:#7c8187;letter-spacing:.6px}
.slider-label{left:393px;font-size:13px;color:var(--white);letter-spacing:.4px}
.track{left:393px;width:239px;height:6px;border-radius:3px;background:linear-gradient(90deg,#3a3a3a 0,#3a3a3a 59%,#e9eef3 59%)}
.thumb{width:12px;height:12px;border-radius:50%;background:#fff;border:1px solid #8a99a8;top:-3px;left:136px}
.scale{left:393px;width:239px;display:flex;justify-content:space-between;font-size:9.6px;color:#9fcbee}
.select{left:392px;top:312px;width:238px;height:32px;background:#f7f7f7;border-radius:3px;font-size:13.5px;color:#6b7077;padding-left:10px;line-height:32px}
.select .caret{position:absolute;right:0;top:6px;width:34px;height:20px;border-left:1px solid #d2d2d2;display:flex;align-items:center;justify-content:center}
.preview{left:695px;top:69px;width:192px;height:192px;border-radius:50%;background:rgba(120,180,225,.45);border:1px solid rgba(180,215,240,.7)}
.total{left:696px;top:313px;width:192px;height:32px;background:var(--navy);border-radius:2px;color:var(--white);font-size:13.5px;line-height:32px;text-align:center;letter-spacing:.3px}

/* enquiry form */
.form-area{left:0;top:496px;width:1024px;height:430px;border-top:2px solid #c9ccd0}
.form-title{left:0;top:30px;width:1020px;text-align:center;font:400 17.6px "Arimo",sans-serif;color:#6a6e73}
.field-label{left:260px;font:400 9.6px "Open Sans",sans-serif;color:#5f646a}
.field{left:259px;width:245px;height:30px;background:#fff;border:1px solid var(--line);border-radius:2px}
.field.focus{border-color:var(--orange)}
.field .ico{position:absolute;left:0;top:0;width:32px;height:100%;display:flex;align-items:center;justify-content:center;border-right:1px dotted #dadada}
.field.area .ico{height:26px}
.captcha{left:521px;top:92px;width:239px;height:94px;background:#fff;border:1px solid #dcdfe2;border-radius:4px;overflow:hidden}
.captcha-art{position:absolute;left:30px;top:12px;width:180px;height:36px;background:#f2f2f2}
.captcha-bar{position:absolute;left:0;bottom:0;width:100%;height:28px;border-top:1px solid #e3e5e7;display:flex;font:600 9px/28px "Open Sans",sans-serif;color:#555}
.captcha-bar span{padding-left:23px;flex:1}
.captcha-bar i{width:30px;border-left:1px solid #e3e5e7;display:flex;align-items:center;justify-content:center}
.check{left:524px;top:284px;width:13px;height:13px;background:#fff;border:1px solid #c9ccd0;border-radius:2px}
.check-text{left:550px;top:284px;font:400 9.6px "Open Sans",sans-serif;color:#666}
.submit{left:519px;top:324px;width:245px;height:39px;background:linear-gradient(#11b0ef,#0a8fd6);border-bottom:3px solid #0b5d9e;border-radius:2px;color:#fff;font:700 14px/36px "Arimo",sans-serif;text-align:center}
.note{left:256px;top:390px;width:512px;text-align:center;font:400 9.6px/14px "Arimo",sans-serif;color:#8b8f94}

/* footer */
.footer{left:0;top:926px;width:1024px;height:238px;background:linear-gradient(#45474b,#323437);border-top:2px solid #2b2c2e}
.col{top:26px;width:170px}
.col h3{font:700 12.8px "Open Sans",sans-serif;color:#fff;padding-bottom:5px;border-bottom:1px solid #575a5e;display:flex;justify-content:space-between;align-items:center}
.col p{font:400 9.6px/14.4px "Open Sans",sans-serif;color:var(--foot-text);margin-top:10px}
.contact-row{display:flex;align-items:center;gap:14px;font:400 9.6px "Open Sans",sans-serif;color:var(--foot-text);margin-top:10px}
.contact-row svg{width:14px}
.news-input{position:absolute;left:0;top:94px;width:238px;height:29px;background:#80868c}
.news-btn{position:absolute;right:0;top:1px;width:63px;height:27px;background:#3f536e;border:1px solid #6f7f93;color:#fff;font:700 9px/25px "Open Sans",sans-serif;text-align:center}
.social-title{position:absolute;left:2px;top:145px;font:700 12.8px "Open Sans",sans-serif;color:#fff}
.social-sq{position:absolute;top:172px;width:27px;height:27px;border-radius:3px;background:#5f7591;border:1px solid #7d8ea3}
.bottom{left:0;top:1164px;width:1024px;height:36px;background:var(--foot-dark);font:400 8px "Arimo",sans-serif;color:#a9adb1}
</style>
</head>
<body>

<div class="abs topbar"></div>
<div class="abs account-tab"><span>Login</span><span>Register</span></div>

<header class="abs header">
  <div class="abs brand" style="top:12px">
    <div class="brand-mark"></div>
    <div class="brand-name">Layerforge Studio</div>
  </div>
  <div class="abs social-top" style="left:593px" role="img" aria-label="Social profile"></div>
  <div class="abs social-top" style="left:621px" role="img" aria-label="Social profile"></div>
  <div class="abs social-top" style="left:649px" role="img" aria-label="Social profile"></div>
  <div class="abs call">
    <svg width="16" height="16" viewBox="0 0 16 16"><rect width="16" height="16" rx="2" fill="#0d3a6e"/><path d="M5 4c1 0 1.5 2 1 2.5l-.6.6c.5 1.2 1.4 2.1 2.6 2.6l.6-.6c.5-.5 2.5 0 2.5 1 0 .8-1 1.5-1.8 1.4C6.6 11.2 4.3 8.9 4 6.1 3.9 5 4.4 4 5 4z" fill="#fff"/></svg>
    <span>Call us today <b>+1800.555.0142</b></span>
  </div>
  <nav class="abs nav">
    <span>Shop</span><span class="sep">|</span><span>What We Do</span><span class="sep">|</span><span class="active">Pricing &amp; Quote</span><span class="sep">|</span><span>Gallery</span><span class="sep">|</span><span>DIY</span><span class="sep">|</span><span>Training</span><span class="sep">|</span><span>Blog</span><span class="sep">|</span><span>Contact Us</span>
  </nav>
</header>
<div class="abs nav-pointer"></div>

<section class="abs quote">
  <h1 class="abs quote-title" style="font-weight:400">Get Instant Quote or</h1>

  <div class="abs mode-btn" style="top:84px">
    <svg width="24" height="22" viewBox="0 0 24 22"><rect x="6" y="1" width="12" height="6" fill="#7c8187"/><rect x="1" y="7" width="22" height="10" rx="2" fill="#7c8187"/><rect x="6" y="13" width="12" height="8" fill="#fff" stroke="#7c8187" stroke-width="2"/></svg>
    Print</div>
  <div class="abs mode-btn" style="top:163px">
    <svg width="22" height="22" viewBox="0 0 22 22" fill="none" stroke="#7c8187" stroke-width="2.5"><circle cx="11" cy="11" r="6"/><path d="M11 1v6M11 15v6M1 11h6M15 11h6"/></svg>
    Scan</div>
  <div class="abs mode-btn" style="top:243px">
    <svg width="26" height="22" viewBox="0 0 26 22" fill="none" stroke="#7c8187" stroke-width="2.5"><rect x="2" y="4" width="17" height="16" rx="3"/><path d="M9 14l1-4 11-9 3 3-11 9z" fill="#7c8187"/></svg>
    Design</div>

  <div class="abs slider-label" style="top:82px">SHAPE</div>
  <div class="abs track" style="top:113px"><div class="abs thumb"></div></div>
  <div class="abs scale" style="top:127px"><span>Square</span><span>Circular</span></div>
  <div class="abs slider-label" style="top:161px">SIZE</div>
  <div class="abs track" style="top:192px"><div class="abs thumb"></div></div>
  <div class="abs slider-label" style="top:241px">VOLUME</div>
  <div class="abs track" style="top:272px"><div class="abs thumb"></div></div>

  <div class="abs select">Material
    <span class="caret"><svg width="11" height="7" viewBox="0 0 11 7"><path d="M1 1l4.5 4.5L10 1" stroke="#555" stroke-width="2" fill="none"/></svg></span>
  </div>

  <div class="abs preview" role="img" aria-label="Live preview of the selected print shape"></div>
  <div class="abs total">Quillmarrow Total: $360</div>
</section>

<section class="abs form-area">
  <h2 class="abs form-title" style="font-weight:400">For further information and inquiries, please fill the form below:</h2>

  <label class="abs field-label" style="top:78px">Your Name</label>
  <div class="abs field focus" style="top:92px"><span class="ico"><svg width="12" height="14" viewBox="0 0 12 14" fill="#c3c6ca"><circle cx="6" cy="4" r="3.3"/><path d="M0 14c0-4 2.5-6 6-6s6 2 6 6z"/></svg></span></div>

  <label class="abs field-label" style="top:140px">Your Phone Number</label>
  <div class="abs field" style="top:157px"><span class="ico"><svg width="13" height="13" viewBox="0 0 13 13"><path d="M2.5 1c1 0 1.8 2.3 1.2 2.9l-.7.7c.6 1.5 1.8 2.7 3.3 3.3l.7-.7c.6-.6 2.9.2 2.9 1.2 0 1-1.1 2-2.2 1.8C4.3 9.7 1.9 7.3 1.1 3.9.9 2.6 1.5 1 2.5 1z" fill="#c3c6ca"/></svg></span></div>

  <label class="abs field-label" style="top:202px">Your Email Address</label>
  <div class="abs field" style="top:218px"><span class="ico"><svg width="15" height="11" viewBox="0 0 15 11"><rect x=".5" y=".5" width="14" height="10" fill="#c3c6ca"/><path d="M1 1l6.5 5L14 1" stroke="#fff" fill="none"/></svg></span></div>

  <label class="abs field-label" style="top:264px">Instructions</label>
  <div class="abs field area" style="top:281px;height:85px"><span class="ico"><svg width="14" height="11" viewBox="0 0 14 11" fill="#c3c6ca"><ellipse cx="7" cy="5" rx="7" ry="4.6"/><path d="M2 8l-1 3 4-2z"/></svg></span></div>

  <div class="abs captcha">
    <div class="captcha-art" role="img" aria-label="Distorted verification words"></div>
    <div class="captcha-bar"><span>Type the above code</span>
      <i><svg width="11" height="11" viewBox="0 0 11 11" fill="none" stroke="#555" stroke-width="1.6"><path d="M9.5 4A4 4 0 0 0 2 3.5M1.5 7A4 4 0 0 0 9 7.5"/></svg></i>
      <i><svg width="12" height="10" viewBox="0 0 12 10"><path d="M1 3h2l3-2v8L3 7H1z" fill="#555"/><path d="M8 3c1 1 1 3 0 4M9.5 1.5c2 2 2 5 0 7" stroke="#555" fill="none"/></svg></i>
      <i><svg width="11" height="11" viewBox="0 0 11 11"><circle cx="5.5" cy="5.5" r="5.5" fill="#555"/><rect x="4.8" y="2.3" width="1.4" height="4.2" fill="#fff"/><rect x="4.8" y="7.5" width="1.4" height="1.4" fill="#fff"/></svg></i>
    </div>
  </div>

  <div class="abs check"><svg width="11" height="11" viewBox="0 0 11 11"><path d="M2 5.5l2.5 2.5L9.5 2" stroke="#444" stroke-width="1.8" fill="none"/></svg></div>
  <div class="abs check-text">I would like to receive promotional material.</div>
  <div class="abs submit">SUBMIT FORM</div>

  <p class="abs note">*Price is indicative only and may be subject ot change. An accurate estimate will be provided upon receiving a print-ready 3D design file.</p>
</section>

<footer class="abs footer">
  <div class="abs col" style="left:137px">
    <h3>About Us <svg width="11" height="13" viewBox="0 0 11 13" fill="#8d9196"><circle cx="5.5" cy="3.5" r="3.2"/><path d="M0 13c0-4 2.5-6 5.5-6S11 9 11 13z"/></svg></h3>
    <p>Duis mollis, est non commodo luctus, nisi erat porttitor ligula, eget lacinia odio sem nec elit. Vestibulum id ligula porta felis euismod semper. Integer posuere erat a ante.</p>
    <p style="margin-top:14px">Vestibulum id ligula porta felis euismod semper. Integer posuere erat a ante.</p>
  </div>

  <div class="abs col" style="left:393px">
    <h3>Contact Details <svg width="15" height="11" viewBox="0 0 15 11"><rect x=".5" y=".5" width="14" height="10" fill="none" stroke="#8d9196"/><path d="M1 1l6.5 5L14 1" stroke="#8d9196" fill="none"/></svg></h3>
    <p>There are many variations of passages of Lorem Ipsum available, but the majority have suffered alteration.</p>
    <div style="margin-top:18px">
      <div class="contact-row"><svg viewBox="0 0 14 14" height="14"><path d="M7 0a4.5 4.5 0 0 1 4.5 4.5C11.5 8 7 14 7 14S2.5 8 2.5 4.5A4.5 4.5 0 0 1 7 0z" fill="#8d9196"/><circle cx="7" cy="4.5" r="1.6" fill="#3e4044"/></svg>Harbor Point</div>
      <div class="contact-row"><svg viewBox="0 0 15 11" height="11"><rect width="15" height="11" fill="#8d9196"/><path d="M.5 .5l7 5.5 7-5.5" stroke="#3e4044" fill="none"/></svg>hello@layerforge.example</div>
      <div class="contact-row"><svg viewBox="0 0 13 13" height="13"><path d="M2.5 1c1 0 1.8 2.3 1.2 2.9l-.7.7c.6 1.5 1.8 2.7 3.3 3.3l.7-.7c.6-.6 2.9.2 2.9 1.2 0 1-1.1 2-2.2 1.8C4.3 9.7 1.9 7.3 1.1 3.9.9 2.6 1.5 1 2.5 1z" fill="#8d9196"/></svg>890-55510-20384</div>
    </div>
  </div>

  <div class="abs col" style="left:648px;width:240px;top:24px">
    <h3>Newsletter Signup <svg width="11" height="11" viewBox="0 0 11 11" fill="#8d9196"><circle cx="1.6" cy="9.4" r="1.6"/><path d="M0 4a7 7 0 0 1 7 7H5.3A5.3 5.3 0 0 0 0 5.7zM0 0a11 11 0 0 1 11 11H9.3A9.3 9.3 0 0 0 0 1.7z"/></svg></h3>
    <p>By subscribing to our mailing list you will get the latest news from us.</p>
    <div class="news-input"><div class="news-btn">Subscribe</div></div>
    <div class="social-title">Get Social</div>
    <div class="social-sq" style="left:1px" role="img" aria-label="Social profile"></div>
    <div class="social-sq" style="left:37px" role="img" aria-label="Social profile"></div>
    <div class="social-sq" style="left:73px" role="img" aria-label="Social profile"></div>
    <div class="social-sq" style="left:109px" role="img" aria-label="Social profile"></div>
  </div>
</footer>

<div class="abs bottom">
  <span class="abs" style="left:135px;top:13px">Copyright 2014 © Layerforge Ltd - All Rights Reserved</span>
  <span class="abs" style="left:787px;top:13px">Site Map &nbsp; &nbsp;•&nbsp; &nbsp; Privacy Policy</span>
</div>

</body>
</html>
```